Home change of address

Martin & Lena Corwick
WE HAVE MOVED
The address of our new home is
Fern Hollow
48 Bramwell Crescent
Ashby on Wold
Warwickshire
B47 3QT
Tel: 07912 484170
Email: martin@lemar.uk.com

```html
<!DOCTYPE html>
<html lang="en">
<head>
<meta charset="utf-8">
<title>We Have Moved – Martin &amp; Lena Corwick</title>
<link rel="stylesheet" href="https://fonts.googleapis.com/css2?family=Montserrat:wght@700&family=Questrial&display=swap">
<style>
  :root {
    --peach: #fcefc9;
    --cream: #fdf9ef;
    --navy: #1b2b50;
    --blue: #5b7df0;
    --sky: #bfe3f5;
    --orange: #f7ab3c;
    --ring-white: #ffffff;
  }
  html, body {
    margin: 0;
    padding: 0;
    overflow: hidden;
    background: var(--peach);
  }
  .card {
    position: relative;
    width: 1015px;
    height: 1200px;
    overflow: hidden;
    background: var(--peach);
    color: var(--navy);
    font-family: "Questrial", sans-serif;
  }
  .backdrop {
    position: absolute;
    inset: 0;
  }
  .text {
    position: absolute;
    margin: 0;
    line-height: 1;
    white-space: nowrap;
  }
  .names {
    top: 108px;
    left: 0;
    width: 100%;
    text-align: center;
    font-size: 50px;
    letter-spacing: 2px;
    word-spacing: 14px;
  }
  .headline {
    top: 232px;
    left: 0;
    width: 100%;
    text-align: center;
    font-family: "Montserrat", sans-serif;
    font-weight: 700;
    font-size: 76px;
    letter-spacing: 1px;
  }
  .intro {
    top: 648px;
    left: 139px;
    font-size: 47px;
  }
  .address {
    font-size: 48px;
    left: 161px;
  }
  .address .county {
    margin-left: 64px;
  }
  .line-1 { top: 756px; }
  .line-2 { top: 825px; }
  .line-3 { top: 893px; }
  .line-4 { top: 958px; }
  .contact {
    position: absolute;
    top: 1070px;
    display: flex;
    align-items: center;
    gap: 8px;
    font-size: 40px;
    line-height: 1;
  }
  .contact svg { flex: none; }
  .contact-phone { left: 44px; }
  .contact-email { left: 429px; }
  .illustration {
    position: absolute;
    border-radius: 40px;
  }
  .illustration-keys {
    left: 24px; top: 342px; width: 435px; height: 250px;
    background: linear-gradient(135deg, rgba(27,43,80,0.55), rgba(91,125,240,0.55) 55%, rgba(191,227,245,0.7));
  }
  .illustration-blossom {
    left: 628px; top: 310px; width: 302px; height: 274px;
    background: linear-gradient(160deg, rgba(27,43,80,0.25), rgba(247,171,60,0.45));
  }
  .illustration-stem {
    left: 0; top: 697px; width: 97px; height: 278px;
    border-radius: 0 40px 40px 0;
    background: linear-gradient(180deg, rgba(247,171,60,0.55), rgba(27,43,80,0.35));
  }
  .illustration-fern {
    left: 902px; top: 1063px; width: 113px; height: 137px;
    border-radius: 40px 0 0 0;
    background: linear-gradient(200deg, rgba(27,43,80,0.12), rgba(27,43,80,0.04));
  }
  .sparkle {
    position: absolute;
    border-radius: 50%;
    background: radial-gradient(circle, rgba(247,171,60,0.9), rgba(247,171,60,0) 70%);
  }
  .sparkle-large { left: 898px; top: 705px; width: 84px; height: 84px; }
  .sparkle-small { left: 99px; top: 867px; width: 38px; height: 38px; }
  .sparkle-bottom { left: 550px; top: 1162px; width: 36px; height: 36px; }
</style>
</head>
<body>
<main class="card">
  <svg class="backdrop" width="1015" height="1200" viewBox="0 0 1015 1200" aria-hidden="true">
    <circle cx="548" cy="991" r="604" fill="var(--cream)"/>
    <g fill="none" stroke-width="1.6">
      <circle cx="478" cy="372" r="16" stroke="var(--ring-white)"/>
      <circle cx="661" cy="375" r="12" stroke="var(--blue)"/>
      <circle cx="955" cy="596" r="17" stroke="var(--ring-white)"/>
      <circle cx="951" cy="673" r="12" stroke="var(--blue)"/>
      <circle cx="673" cy="727" r="12" stroke="var(--blue)"/>
      <circle cx="125" cy="828" r="12" stroke="var(--blue)"/>
      <circle cx="399" cy="1180" r="12" stroke="var(--blue)"/>
    </g>
  </svg>

  <div class="illustration illustration-keys" role="img" aria-label="Illustration of a house key on a ring with a small blue house"></div>
  <div class="illustration illustration-blossom" role="img" aria-label="Illustration of an orange flower with navy leaves and a fern sprig"></div>
  <div class="illustration illustration-stem" role="img" aria-label="Illustration of an orange flower on a tall stem with leaves"></div>
  <div class="illustration illustration-fern" role="img" aria-label="Illustration of an outlined fern sprig"></div>
  <div class="sparkle sparkle-large" role="img" aria-label="Orange sparkle"></div>
  <div class="sparkle sparkle-small" role="img" aria-label="Orange sparkle"></div>
  <div class="sparkle sparkle-bottom" role="img" aria-label="Orange sparkle"></div>

  <p class="text names">Martin &amp; Lena Corwick</p>
  <h1 class="text headline">WE HAVE MOVED</h1>
  <p class="text intro">The address of our new home is</p>

  <address class="address-block" style="font-style:normal">
    <p class="text address line-1">Fern Hollow</p>
    <p class="text address line-2">48 Bramwell Crescent</p>
    <p class="text address line-3">Ashby on Wold<span class="county">Warwickshire</span></p>
    <p class="text address line-4">B47 3QT</p>
  </address>

  <p class="contact contact-phone">
    <svg width="46" height="50" viewBox="0 0 24 24" aria-label="Telephone" role="img">
      <path fill="var(--navy)" d="M6.6 10.8c1.4 2.8 3.8 5.1 6.6 6.6l2.2-2.2c.3-.3.7-.4 1-.2 1.1.4 2.3.6 3.6.6.6 0 1 .4 1 1V20c0 .6-.4 1-1 1C10.6 21 3 13.4 3 4c0-.6.4-1 1-1h3.5c.6 0 1 .4 1 1 0 1.3.2 2.5.6 3.6.1.3 0 .7-.2 1l-2.3 2.2z"/>
    </svg>
    <span>07912 484170</span>
  </p>
  <p class="contact contact-email">
    <svg width="44" height="34" viewBox="0 0 44 34" aria-label="Email" role="img">
      <rect x="1" y="3" width="42" height="28" rx="2" fill="var(--navy)"/>
      <path d="M3 5 L22 19 L41 5 M3 29 L17 16 M41 29 L27 16" stroke="var(--cream)" stroke-width="2.5" fill="none"/>
    </svg>
    <span>martin@lemar.uk.com</span>
  </p>
</main>
</body>
</html>
```